Webbanner-Design
Verkauf von Pools und Zubehör
Es soll ein Banner für unseren Shop sein für eine Aktion, dass Holzpools jetzt sofort lieferbar sind Text:
Verschönern Sie doch Ihren Garten: Holzpools sofort lieferbar!
Unseren Shop finden Sie unter www.brunnkarst17.de
Fotos können von unserer Seite www.brunnkarst17-gallery.de verwendet werden
Das angefügte Bild sollte ebenfalls dabei sein. Hintergrund: die Leute sollen wegen Corona zu Hause bleiben und haben Zeit, daher sind unsere sofort lieferbaren Pools jetzt natürlich gut. Ich bin auch für abweichende Texte offen.

```html
<!DOCTYPE html>
<html lang="de">
<head>
<meta charset="utf-8">
<title>Brunnkarst17 – Holzpools sofort lieferbar</title>
<link rel="stylesheet" href="https://fonts.googleapis.com/css2?family=Open+Sans:wght@400;600;700;800&display=swap">
<style>
  :root{
    --topbar:#06b6e6;
    --water-a:#0b7fc4;
    --water-b:#2bb3ea;
    --page-grey:#ededed;
    --white:#ffffff;
    --text:#333333;
    --muted:#555555;
    --line:#dddddd;
    --navy:#0a0d78;
    --accent:#18aee8;
    --badge:#1e4f9e;
  }
  *{box-sizing:border-box;margin:0;padding:0}
  html,body{width:1200px;height:1023px;overflow:hidden}
  body{position:relative;background:var(--page-grey);font-family:"Open Sans",Arial,sans-serif;color:var(--text)}
  .water-backdrop{position:absolute;left:0;top:0;width:1200px;height:577px;background:linear-gradient(135deg,var(--water-a),var(--water-b) 45%,var(--water-a))}
  .page{position:absolute;left:99px;top:0;width:1002px;height:1023px;background:var(--white)}
  .service-bar{position:absolute;left:0;top:0;width:1002px;height:32px;background:var(--topbar);color:var(--white);font-size:12.5px}
  .service-bar span{position:absolute;top:8px;display:flex;align-items:center;gap:4px;white-space:nowrap}
  .service-bar svg{width:11px;height:11px}
  .meta-links{position:absolute;right:26px;top:43px;font-size:10.5px;display:flex}
  .meta-links a{color:var(--text);text-decoration:none;padding:0 5px;border-left:1px solid var(--line)}
  .meta-links a:first-child{border-left:none}
  .brand{position:absolute;left:24px;top:82px;display:flex;align-items:center;gap:8px;font-size:25px;font-weight:700;color:#1b5fb8}
  .brand i{width:20px;height:20px;border-radius:50%;background:var(--accent);display:block}
  .search{position:absolute;left:548px;top:90px;width:222px;height:31px;display:flex;border:1px solid #ccc;border-radius:3px}
  .search span{flex:1;padding:6px 11px;font-size:12.5px;color:#999;border-right:1px solid #ccc}
  .search b{width:37px;display:flex;align-items:center;justify-content:center;background:#f8f8f8}
  .account{position:absolute;left:795px;top:97px;font-size:13px;display:flex;gap:26px}
  .main-nav{position:absolute;left:0;top:174px;width:1002px;height:45px;border-top:3px solid #e6e6e6;border-bottom:2px solid #e6e6e6;display:flex;align-items:center;padding-left:24px;gap:21px;font-size:12.5px;color:var(--muted)}
  .promo{position:absolute;left:20px;top:241px;width:962px;height:324px}
  .carousel-dots{position:absolute;left:455px;top:592px;display:flex;gap:15px;align-items:center}
  .carousel-dots i{width:7px;height:7px;border-radius:50%;background:#444;display:block}
  .carousel-dots i.active{width:10px;height:10px;background:none;border:2px solid #444}
  .divider{position:absolute;left:22px;top:642px;width:958px;border-top:1px solid var(--line)}
  .section-title{position:absolute;left:22px;top:657px;font-size:23px;font-weight:400;color:var(--text)}
  .category{position:absolute;top:756px;width:264px;text-align:center;font-size:12.5px}
  .category .photo{width:264px;height:198px}
  .category p{margin-top:42px}
</style>
</head>
<body>
<div class="water-backdrop" role="img" aria-label="Hintergrundfoto: bewegte blaue Poolwasseroberfläche"></div>

<div class="page">
  <div class="service-bar">
    <span style="left:95px"><svg viewBox="0 0 12 12"><path fill="#fff" d="M2.5 1l2 2-1 1.3a6 6 0 0 0 4.2 4.2L9 7.5l2 2-1.5 1.5C5 11 1 7 1 2.5z"/></svg>+49 (0) 5124 / 381 706 2</span>
    <span style="left:334px"><svg viewBox="0 0 12 12"><rect width="12" height="12" rx="2" fill="#fff"/><path d="M3 6l2 2 4-4" stroke="#06b6e6" stroke-width="1.8" fill="none"/></svg>persönliche Beratung</span>
    <span style="left:580px"><svg viewBox="0 0 12 12"><rect width="12" height="12" rx="2" fill="#fff"/><path d="M3 6l2 2 4-4" stroke="#06b6e6" stroke-width="1.8" fill="none"/></svg>sicher Einkaufen</span>
    <span style="left:812px"><svg viewBox="0 0 12 12"><circle cx="6" cy="6" r="6" fill="#fff"/><path d="M3 6h5M6 3.5L8.5 6 6 8.5" stroke="#06b6e6" stroke-width="1.6" fill="none"/></svg>Brunnkarst-Galerie</span>
  </div>

  <nav class="meta-links">
    <a>Startseite</a><a>Mein Konto</a><a>Kontakt</a><a>Unsere Partner</a><a>Bildergalerie</a><a>Wir über uns</a><a>News</a>
  </nav>

  <div class="brand"><i></i>Brunnkarst17</div>

  <div class="search"><span>Suchen</span><b><svg width="15" height="15" viewBox="0 0 16 16"><circle cx="6.5" cy="6.5" r="5" stroke="#18aee8" stroke-width="2.2" fill="none"/><path d="M10 10l4.5 4.5" stroke="#18aee8" stroke-width="2.4"/></svg></b></div>

  <div class="account"><span>👤 Anmelden ▾</span><span>🛒 0,00 € ▾</span></div>

  <nav class="main-nav">
    <span>Sonderangebote</span><span>Pool &amp; Zubehör ▾</span><span>Sauna ▾</span><span>Infrarot ▾</span><span>Holzbadewannen</span>
  </nav>

  <svg class="promo" viewBox="0 0 962 324" aria-label="Aktionsbanner Holzpools sofort lieferbar">
    <defs>
      <linearGradient id="garden" x1="0" y1="0" x2="0" y2="1">
        <stop offset="0" stop-color="#5f7a3a"/><stop offset="0.4" stop-color="#2f8ee0"/><stop offset="0.6" stop-color="#b08a55"/><stop offset="1" stop-color="#c9a66e"/>
      </linearGradient>
    </defs>
    <rect width="962" height="324" fill="var(--navy)"/>
    <path d="M448 0H962V324H430C400 270 385 200 405 140 415 90 430 40 448 0Z" fill="url(#garden)" role="img" aria-label="Foto: achteckiger Holzpool mit Leiter in einem Garten vor einer Ziegelmauer"/>
    <path d="M440 0h9C430 40 415 90 405 140 385 200 400 270 430 324h-9C392 270 378 200 398 140 408 90 422 40 440 0Z" fill="#fff"/>
    <g font-family="Open Sans, Arial, sans-serif" font-weight="800">
      <text x="42" y="106" font-size="27" fill="#fff">VERSCHÖNERN SIE</text>
      <text x="42" y="138" font-size="27" fill="#fff">DOCH IHREN GARTEN</text>
      <text x="41" y="202" font-size="45" fill="var(--accent)">HOLZPOOLS</text>
      <text x="41" y="244" font-size="45" fill="var(--accent)">SOFORT</text>
      <text x="41" y="286" font-size="45" fill="var(--accent)">LIEFERBAR!</text>
    </g>
    <rect x="763" y="126" width="191" height="191" fill="var(--badge)" role="img" aria-label="Platz für ein Kampagnenabzeichen"/>
  </svg>

  <div class="carousel-dots"><i></i><i class="active"></i><i></i><i></i><i></i></div>

  <div class="divider"></div>
  <h2 class="section-title">Unsere TOP-Kategorien</h2>

  <div class="category" style="left:42px">
    <div class="photo" role="img" aria-label="Foto: Holzpool auf Holzterrasse im Garten" style="background:linear-gradient(180deg,#4f7a34,#3a8fd8 50%,#8ea64f)"></div>
    <p>Holzpools</p>
  </div>
  <div class="category" style="left:369px">
    <div class="photo" role="img" aria-label="Foto: blaue Poolabdeckung auf einem gepflasterten Pool" style="background:linear-gradient(90deg,#9a9a92,#1f9be6 25%,#1f9be6 75%,#9a9a92)"></div>
    <p>Poolabdeckungen</p>
  </div>
  <div class="category" style="left:697px">
    <div class="photo" role="img" aria-label="Foto: Rollladenabdeckung an einem Pool mit Natursteinrand" style="background:linear-gradient(160deg,#4a5a3a,#cfe3ee 40%,#2f7fd6 65%,#8b8b86)"></div>
    <p>Oberflur</p>
  </div>
</div>
</body>
</html>
```